Business Card for a New Zealand IT Startup

I need a business card for VELTA Holdings. We are a young startup based in New Zealand working in internet marketing and web development. The design should have some element connected to New Zealand, such as wave, koru or silver fern, just don't use a kiwi bird.

```html
<!DOCTYPE html>
<html lang="en">
<head>
<meta charset="utf-8">
<title>VELTA Holdings – Business Card</title>
<link rel="stylesheet" href="https://fonts.googleapis.com/css2?family=Open+Sans:wght@400;600;700&display=swap">
<style>
  :root {
    --backdrop: #3a3a3c;
    --card: #1e1e20;
    --blue: #1f7fcb;
    --orange: #f0672a;
    --white: #f2f2f2;
  }
  * { box-sizing: border-box; margin: 0; padding: 0; }
  html, body { width: 799px; height: 1200px; overflow: hidden; }
  body {
    background: var(--backdrop);
    font-family: "Open Sans", Arial, sans-serif;
    color: var(--white);
    position: relative;
  }
  .card {
    position: absolute;
    left: 90px;
    width: 620px;
    height: 360px;
    background: var(--card);
    border-radius: 26px;
    box-shadow: 0 10px 30px rgba(0,0,0,0.45);
    overflow: hidden;
  }
  .card--front { top: 150px; }
  .card--back { top: 690px; }

  .brand {
    position: absolute;
    display: flex;
    align-items: center;
    gap: 14px;
  }
  .brand__name {
    color: var(--blue);
    font-weight: 700;
    letter-spacing: 2px;
    text-transform: uppercase;
    line-height: 1;
    white-space: nowrap;
  }
  .brand__dot { border-radius: 50%; background: var(--blue); flex: none; }
  .card--front .brand { left: 0; right: 0; top: 118px; justify-content: center; }
  .card--front .brand__name { font-size: 44px; }
  .card--front .brand__dot { width: 38px; height: 38px; }

  .wave-rule { display: block; fill: none; stroke-width: 3; stroke-linecap: round; }
  .wave-rule--blue { stroke: var(--blue); }
  .wave-rule--orange { stroke: var(--orange); }

  .site-line {
    position: absolute;
    left: 0; right: 0; bottom: 62px;
    display: flex; align-items: center; justify-content: center; gap: 16px;
    font-size: 17px;
  }
  .site-line .wave-rule { width: 60px; height: 12px; }
  .site-line .accent-blue { color: var(--blue); }
  .site-line .accent-orange { color: var(--orange); }

  .sea {
    position: absolute; left: 0; right: 0; bottom: 0; width: 620px; height: 40px;
  }

  .card--back .brand { left: 0; right: 0; top: 52px; justify-content: center; padding-left: 120px; }
  .card--back .brand__name { font-size: 32px; }
  .card--back .brand__dot { width: 28px; height: 28px; }

  .rule-top {
    position: absolute; left: 30px; right: 30px; top: 140px; height: 2px;
    background: linear-gradient(90deg, var(--orange), var(--blue));
  }
  .rule-bottom {
    position: absolute; left: 230px; bottom: 38px; width: 360px; height: 14px;
  }
  .person { position: absolute; left: 40px; top: 158px; text-align: right; width: 240px; }
  .person__name { color: var(--blue); font-size: 24px; font-weight: 700; line-height: 1.2; }
  .person__title { font-size: 14px; margin-top: 2px; }

  .contacts { position: absolute; left: 305px; top: 168px; list-style: none; }
  .contacts li { display: flex; align-items: center; gap: 12px; font-size: 16px; line-height: 26px; }
  .contacts svg { width: 15px; height: 15px; fill: var(--orange); flex: none; }

  .address { position: absolute; left: 40px; top: 262px; font-size: 16px; }
</style>
</head>
<body>
  <section class="card card--front" aria-label="Card front">
    <div class="brand">
      <span class="brand__dot"></span>
      <span class="brand__name">Velta Holdings</span>
    </div>
    <div class="site-line">
      <svg class="wave-rule wave-rule--blue" viewBox="0 0 60 12" aria-hidden="true"><path d="M2 6 Q9.5 0 17 6 T32 6 T47 6 T58 4"/></svg>
      <span>www.<span class="accent-blue">velta</span><span class="accent-orange">holdings</span>.com</span>
      <svg class="wave-rule wave-rule--blue" viewBox="0 0 60 12" aria-hidden="true"><path d="M2 6 Q9.5 0 17 6 T32 6 T47 6 T58 4"/></svg>
    </div>
    <svg class="sea" viewBox="0 0 620 40" preserveAspectRatio="none" aria-hidden="true">
      <path class="wave-rule wave-rule--blue" d="M0 24 Q38 10 77 24 T155 24 T232 24 T310 24 T387 24 T465 24 T542 24 T620 24"/>
      <path class="wave-rule wave-rule--orange" d="M0 32 Q38 20 77 32 T155 32 T232 32 T310 32 T387 32 T465 32 T542 32 T620 32"/>
    </svg>
  </section>

  <section class="card card--back" aria-label="Card back">
    <div class="brand">
      <span class="brand__dot"></span>
      <span class="brand__name">Velta Holdings</span>
    </div>
    <div class="rule-top"></div>
    <div class="person">
      <p class="person__name">Mara Kealy</p>
      <p class="person__title">Managing Director</p>
    </div>
    <ul class="contacts">
      <li><svg viewBox="0 0 24 24" aria-hidden="true"><path d="M6.6 10.8a15 15 0 0 0 6.6 6.6l2.2-2.2c.3-.3.7-.4 1-.2 1.1.4 2.3.6 3.6.6.6 0 1 .4 1 1V20c0 .6-.4 1-1 1A17 17 0 0 1 3 4c0-.6.4-1 1-1h3.5c.6 0 1 .4 1 1 0 1.3.2 2.5.6 3.6.1.3 0 .7-.2 1z"/></svg>555-0142-318</li>
      <li><svg viewBox="0 0 24 24" aria-hidden="true"><path d="M2 5h20v14H2zm2 2v.5l8 5 8-5V7l-8 5z"/></svg>hello@veltaholdings.com</li>
      <li><svg viewBox="0 0 24 24" aria-hidden="true"><path d="M12 2a10 10 0 1 0 0 20 10 10 0 0 0 0-20zm6.9 6h-3a15 15 0 0 0-1.3-3.9A8 8 0 0 1 18.9 8zM12 4c.8 1.2 1.5 2.5 1.9 4h-3.8c.4-1.5 1.1-2.8 1.9-4zM4.3 14a8 8 0 0 1 0-4h3.4a16 16 0 0 0 0 4zm.8 2h3a15 15 0 0 0 1.3 3.9A8 8 0 0 1 5.1 16zm3-8h-3a8 8 0 0 1 4.3-3.9C8.8 5.3 8.4 6.6 8.1 8zM12 20c-.8-1.2-1.5-2.5-1.9-4h3.8c-.4 1.5-1.1 2.8-1.9 4zm2.3-6H9.7a14 14 0 0 1 0-4h4.6a14 14 0 0 1 0 4zm.3 5.9c.6-1.2 1-2.5 1.3-3.9h3a8 8 0 0 1-4.3 3.9zm1.7-5.9a16 16 0 0 0 0-4h3.4a8 8 0 0 1 0 4z"/></svg>www.veltaholdings.com</li>
    </ul>
    <p class="address">48 Harbour Lane, Any Town, Any City, NZ 654321</p>
    <svg class="rule-bottom wave-rule wave-rule--blue" viewBox="0 0 360 14" preserveAspectRatio="none" aria-hidden="true">
      <path d="M2 7 Q24 1 46 7 T90 7 T134 7 T178 7 T222 7 T266 7 T310 7 T358 7"/>
    </svg>
  </section>
</body>
</html>
```